Organization and people consulting firm needs a website design

I need a website that promotes and explains the consulting service we will provide. The organization is called Bluefinch Advisory Partners. Our services include organization design, employee experience, change management, and executive coaching. I would like to see a simple clean and professional design, that reflects a modern and forward looking professional services company

Target Market(s)

Mid market and large companies

Industry/Entity Type

Management Consulting

Coding

Coded - Design and coding required

Number of Pages Required

5+ page

Font styles to use
Sans Serif

Colors

Designer to choose colors to be used in the design.

Requirements
Must have
• The following pages: Home, The Way We Work, What We Do, Our Founder, Insights, Contact.
• Search button.
• Hyper links (will be provided with main body text)
• Scrolling website with summaries at top level and links to more detail at lower level (like this website: veltracore.com)
• Company logo (uploaded)
• I have text for each of the pages that I can upload once the basic design is done
Should not have
• No clutter, keep the design clean

```html
<!DOCTYPE html>
<html lang="en">
<head>
<meta charset="utf-8">
<title>Bluefinch Advisory Partners</title>
<link href="https://fonts.googleapis.com/css2?family=Cinzel:wght@400;600&family=Open+Sans:wght@400;600;700&display=swap" rel="stylesheet">
<style>
:root{
  --red:#d8102d;
  --red-dark:#b80a24;
  --ink:#333333;
  --grey:#777777;
  --light:#f1f1f1;
  --band:#e7e7e7;
  --dark:#2b2b2b;
  --white:#ffffff;
}
*{box-sizing:border-box;margin:0;padding:0}
html,body{width:1200px;height:3240px;overflow:hidden;background:var(--white)}
body{font-family:"Open Sans",Arial,sans-serif;color:var(--ink);position:relative}
.abs{position:absolute}

/* nav */
.nav{left:0;top:0;width:1200px;height:48px;background:rgba(20,20,20,.75);z-index:3;display:flex;justify-content:center;align-items:center;gap:6px}
.nav a{color:var(--white);text-decoration:none;font-size:12px;font-weight:600;letter-spacing:.5px;padding:16px 16px}
.nav a.active{background:var(--red)}

/* hero */
.hero-photo{left:0;top:0;width:1200px;height:760px;background:linear-gradient(180deg,#55595e 0%,#6f7378 40%,#4a4d52 100%)}
.hero-shade{left:0;top:0;width:1200px;height:760px;background:rgba(0,0,0,.35)}
.brand{left:0;top:170px;width:1200px;display:flex;justify-content:center;align-items:center;gap:14px;color:var(--white)}
.brand-mark{width:34px;height:34px;background:var(--white)}
.brand-name{font-family:"Open Sans",Arial,sans-serif;font-weight:600;font-size:30px;color:var(--white)}
.hero-title{left:0;top:272px;width:1200px;text-align:center;color:var(--white);font-family:"Cinzel",Georgia,serif}
.hero-title .l1{font-size:38px;letter-spacing:2px}
.hero-title .l2{font-size:46px;letter-spacing:2px;margin-top:4px}
.dots{left:0;top:602px;width:1200px;display:flex;justify-content:center;gap:10px}
.dots i{width:10px;height:10px;border-radius:50%;background:rgba(255,255,255,.6)}
.dots i.on{background:var(--white)}

/* section numbers */
.num{left:150px;font-size:38px;font-weight:700;color:var(--ink)}
.num.light{color:var(--white)}
.pager{left:166px;display:flex;flex-direction:column;gap:9px}
.pager i{width:9px;height:9px;border-radius:50%;background:#cfcfcf}
.pager i.on{background:var(--red)}
.pager.light i{background:rgba(255,255,255,.55)}
.pager.light i.on{background:var(--white)}

.section-title{left:0;width:1200px;text-align:center;font-size:30px;font-weight:700;color:#4a4a4a;letter-spacing:.5px}
.section-title.white{color:var(--white)}
.section-title.red{color:var(--red)}
.copy{font-size:14px;line-height:24px;color:var(--grey)}
.center{text-align:center}

/* what we do */
.service{width:220px;color:var(--white)}
.service h3{font-size:15px;font-weight:700;letter-spacing:.3px}
.service p{font-size:12px;line-height:18px;opacity:.9;margin-top:4px}
.service.left{text-align:right}

/* founder */
.founder-photo{left:210px;top:1790px;width:300px;height:300px;border-radius:50%;background:radial-gradient(circle at 50% 40%,#b9b4ae,#6d6a66);border:6px solid var(--white);box-shadow:0 0 0 2px #ddd}
.founder-name{left:600px;top:1830px;font-size:20px;font-weight:700;color:var(--red)}

/* insights */
.card{top:2400px;width:236px;height:260px;overflow:hidden}
.card-photo{width:100%;height:100%}
.card-caption{position:absolute;left:0;bottom:0;width:100%;padding:16px;color:var(--white);font-size:14px;font-weight:600;line-height:20px;background:rgba(0,0,0,.55)}
.card.red{background:var(--red)}
.card.red .card-caption{background:none;top:20px;bottom:auto}

/* contact */
.contact-row{left:0;top:2872px;width:1200px;display:flex;justify-content:center;gap:60px;font-size:12px;color:var(--grey);align-items:center}
.contact-row span{display:flex;align-items:center;gap:8px}
.field{height:34px;border:1px solid #d6d6d6;background:var(--white);font-size:12px;color:#999;padding:9px 12px}
.submit{left:535px;top:3098px;width:130px;height:36px;background:var(--red);color:var(--white);font-size:13px;font-weight:700;letter-spacing:1px;display:flex;align-items:center;justify-content:center}
.social{display:flex;gap:12px}
.social i{width:26px;height:26px;border-radius:50%;background:var(--ink)}

.footer{left:0;top:3180px;width:1200px;height:60px;background:var(--dark);color:#aaa;font-size:11px;letter-spacing:.5px;display:flex;align-items:center;justify-content:center}
</style>
</head>
<body>

<!-- Hero -->
<div class="abs hero-photo" role="img" aria-label="Photo of business consultants meeting around a table"></div>
<div class="abs hero-shade"></div>
<nav class="abs nav">
  <a href="#home">HOME</a>
  <a href="#way">THE WAY WE WORK</a>
  <a href="#what">WHAT WE DO</a>
  <a href="#founder" class="active">OUR FOUNDER</a>
  <a href="#insights">INSIGHTS</a>
  <a href="#contact">CONTACT</a>
</nav>
<div class="abs num light" style="top:196px">01</div>
<div class="abs pager light" style="top:254px"><i class="on"></i><i></i><i></i><i></i><i></i></div>
<div class="abs brand"><span class="brand-mark"></span><span class="brand-name">Bluefinch Advisory Partners</span></div>
<h1 class="abs hero-title"><div class="l1">WE ARE ORGANISATION &amp;</div><div class="l2">PEOPLE CONSULTING FIRM</div></h1>
<div class="abs dots"><i class="on"></i><i></i><i></i><i></i></div>

<!-- The Way We Work -->
<h2 class="abs section-title" style="top:800px">THE WAY WE WORK</h2>
<div class="abs num" style="top:776px">02</div>
<div class="abs pager" style="top:834px"><i></i><i class="on"></i><i></i><i></i></div>
<p class="abs copy center" style="left:300px;top:856px;width:600px">We design organisations around people, pairing clear structures with practical insight so teams can deliver lasting results.</p>
<p class="abs copy center" style="left:300px;top:920px;width:600px">Every engagement starts with listening. We map how work really flows, test ideas with the people who do it, and shape a plan that leaders can own. Our approach keeps change simple, measurable and grounded in the culture you already have, so progress continues long after we step back.</p>

<!-- What We Do -->
<svg class="abs" style="left:0;top:1040px" width="1200" height="620" viewBox="0 0 1200 620">
  <polygon points="0,60 1200,10 1200,540 0,600" fill="var(--red)"/>
  <polygon points="0,560 1200,500 1200,540 0,600" fill="var(--red-dark)"/>
  <polygon points="0,40 1200,0 1200,10 0,60" fill="#f0b7c0"/>
  <g stroke="#ffffff" stroke-width="1.5" fill="none" opacity=".8">
    <line x1="400" y1="318" x2="540" y2="318"/>
    <line x1="400" y1="450" x2="470" y2="450"/><line x1="470" y1="450" x2="540" y2="390"/>
    <line x1="800" y1="318" x2="660" y2="318"/>
    <line x1="800" y1="450" x2="730" y2="450"/><line x1="730" y1="450" x2="660" y2="390"/>
  </g>
  <circle cx="600" cy="350" r="62" fill="none" stroke="#ffffff" stroke-width="2"/>
  <!-- org design icon -->
  <g stroke="#fff" stroke-width="2" fill="none" transform="translate(420,296)">
    <rect x="14" y="0" width="16" height="12"/><rect x="0" y="30" width="14" height="12"/><rect x="30" y="30" width="14" height="12"/>
    <path d="M22 12v9M7 21h30M7 21v9M37 21v9"/>
  </g>
  <!-- employee experience icon -->
  <g stroke="#fff" stroke-width="2" fill="none" transform="translate(420,428)">
    <circle cx="14" cy="10" r="7"/><path d="M2 40c0-12 24-12 24 0"/><circle cx="32" cy="12" r="6"/><path d="M26 28c8-4 18 0 18 10"/>
  </g>
  <!-- change management icon -->
  <g stroke="#fff" stroke-width="2" fill="none" transform="translate(736,296)">
    <path d="M6 20a16 16 0 0 1 28-10"/><path d="M34 2v8h-8"/><path d="M38 24a16 16 0 0 1-28 10"/><path d="M10 42v-8h8"/>
  </g>
  <!-- executive coaching icon -->
  <g stroke="#fff" stroke-width="2" fill="none" transform="translate(736,428)">
    <rect x="0" y="2" width="28" height="20" rx="3"/><path d="M6 22v8l8-8"/><rect x="16" y="16" width="28" height="20" rx="3"/>
  </g>
</svg>
<div class="abs num light" style="top:1200px">03</div>
<div class="abs pager light" style="top:1258px"><i></i><i></i><i class="on"></i><i></i></div>
<h2 class="abs section-title white" style="top:1108px">WHAT WE DO</h2>
<p class="abs copy center" style="left:330px;top:1152px;width:540px;color:#fff">Four connected services that help mid market and large companies align structure, people and leadership for the future.</p>
<div class="abs service left" style="left:180px;top:1326px"><h3>ORGANISATION DESIGN</h3><p>Structures, roles and decision rights built for growth.</p></div>
<div class="abs service left" style="left:180px;top:1460px"><h3>EMPLOYEE EXPERIENCE</h3><p>Moments that matter, shaped around your people.</p></div>
<div class="abs service" style="left:800px;top:1326px"><h3>CHANGE MANAGEMENT</h3><p>Guiding teams through transitions with clarity.</p></div>
<div class="abs service" style="left:800px;top:1460px"><h3>EXECUTIVE COACHING</h3><p>One to one coaching for leaders facing new challenges.</p></div>

<!-- Our Founder -->
<div class="abs num" style="top:1636px">04</div>
<div class="abs pager" style="top:1694px"><i></i><i></i><i></i><i class="on"></i></div>
<h2 class="abs section-title" style="top:1660px">OUR FOUNDER</h2>
<div class="abs founder-photo" role="img" aria-label="Portrait photo of the firm's founder"></div>
<div class="abs founder-name">FOUNDER NAME</div>
<p class="abs copy" style="left:600px;top:1872px;width:420px">Twenty years advising boards and executive teams on organisation design, culture and leadership across Europe and North America.</p>
<p class="abs copy" style="left:600px;top:1960px;width:420px">Before founding the firm she led people strategy for global businesses, guiding major restructures and building leadership programmes. Today she works side by side with clients to turn complex change into clear, human steps.</p>

<!-- Insights -->
<svg class="abs" style="left:0;top:2130px" width="1200" height="640" viewBox="0 0 1200 640">
  <polygon points="0,40 1200,0 1200,590 0,630" fill="var(--band)"/>
</svg>
<div class="abs social" style="left:1000px;top:2178px"><i></i><i></i><i></i></div>
<div class="abs num" style="top:2264px">05</div>
<div class="abs pager" style="top:2322px"><i></i><i></i><i></i><i></i><i class="on"></i></div>
<h2 class="abs section-title" style="top:2262px">INSIGHTS</h2>
<p class="abs copy center" style="left:340px;top:2310px;width:520px">Ideas, research and practical guides on organisation design, people and leadership from our consulting team.</p>
<article class="abs card" style="left:260px">
  <div class="card-photo" role="img" aria-label="Photo of colleagues discussing at a laptop" style="background:linear-gradient(160deg,#6e7c8c,#3d4650)"></div>
  <div class="card-caption">Designing teams for hybrid work</div>
</article>
<article class="abs card red" style="left:512px">
  <div class="card-caption">Why change programmes stall and how to restart them</div>
</article>
<article class="abs card" style="left:764px">
  <div class="card-photo" role="img" aria-label="Photo of a handshake across a desk" style="background:linear-gradient(160deg,#c9b9a3,#7b6a57)"></div>
  <div class="card-caption">Coaching leaders through growth</div>
</article>

<!-- Contact -->
<div class="abs num" style="top:2784px">06</div>
<div class="abs pager" style="top:2842px"><i></i><i></i><i></i><i></i><i></i><i class="on"></i></div>
<h2 class="abs section-title red" style="top:2800px">CONTACT</h2>
<div class="abs contact-row">
  <span><svg width="14" height="18" viewBox="0 0 14 18"><path d="M7 1a6 6 0 0 0-6 6c0 5 6 10 6 10s6-5 6-10a6 6 0 0 0-6-6z" fill="var(--grey)"/><circle cx="7" cy="7" r="2" fill="#fff"/></svg>218 Harlow Street, Denton TX 76201</span>
  <span><svg width="16" height="16" viewBox="0 0 16 16"><path d="M3 1h3l1.5 4-2 1.2a9 9 0 0 0 4.3 4.3L11 8.5l4 1.5v3a2 2 0 0 1-2 2A12 12 0 0 1 1 3a2 2 0 0 1 2-2z" fill="var(--grey)"/></svg>(555) 014-2280</span>
  <span><svg width="18" height="14" viewBox="0 0 18 14"><rect x="1" y="1" width="16" height="12" fill="none" stroke="var(--grey)" stroke-width="1.5"/><path d="M1 1l8 7 8-7" fill="none" stroke="var(--grey)" stroke-width="1.5"/></svg>hello@bluefinchadvisory.com</span>
</div>
<div class="abs field" style="left:356px;top:2946px;width:156px">Your Name</div>
<div class="abs field" style="left:522px;top:2946px;width:156px">Email address</div>
<div class="abs field" style="left:688px;top:2946px;width:156px">Phone number</div>
<div class="abs field" style="left:356px;top:2994px;width:488px;height:86px">Message</div>
<div class="abs submit">SUBMIT</div>

<footer class="abs footer">© 2020 BLUEFINCH ADVISORY PARTNERS. ALL RIGHT RESERVED</footer>

</body>
</html>
```